NEW Modern Sleek Business Card for VR Language Startup

Our startup is using VR to lead the next wave of world language education. We need a two-sided business card that introduces the larger organization (Brightloom Language Inc) and our contact info on one side and shows the product, Glimwoorld, on the other side.

Side 1 (contact info)= Brightloom Logo and Contact info (name, title, phone, email)

Side 2 (product)= Glimworld logo, text, and website
Text= Culturally Immersive Language Learning Games
Website= www.glimworld-play.com

Target Market(s)

Education, Technology

Contact Information for Business Card

Contact info will be updated upon approval of the design. For now, put this as a placeholder.

Perry Dunmore
Founder & CEO
pdunmore@quillpost-mail.net
(555)-014-2286

Font styles to use
Other font styles liked:
• Gibson and Century Gothic are the brand fonts

Requirements
Nice to have
• I would love to see cohesion between the design and colors of the two logos. I have attached a few business card designs that I like, so you can get a feel for my preferred style.

```html
<!DOCTYPE html>
<html lang="en">
<head>
<meta charset="utf-8">
<title>Brightloom Language — Business Card</title>
<link rel="stylesheet" href="https://fonts.googleapis.com/css2?family=Montserrat:wght@400;600;700&family=Questrial&display=swap">
<style>
  :root {
    --stage: #2b2c2f;
    --card-white: #ffffff;
    --ink-dark: #1d1d1f;
    --accent-cyan: #27aee0;
    --grad-purple: #5a58a6;
    --grad-blue: #5a86c6;
    --grad-cyan: #5cc8da;
    --tagline: #4b57a3;
    --warm-orange: #f0683a;
    --warm-red: #e83d5f;
    --mid-violet: #7a4fa6;
    --cool-blue: #2fb8ea;
  }
  * { box-sizing: border-box; margin: 0; padding: 0; }
  html, body {
    width: 1200px; height: 900px; overflow: hidden;
    background: var(--stage);
  }
  .canvas {
    position: relative; width: 1200px; height: 900px;
  }
  .card {
    position: absolute; width: 560px; height: 320px;
    border-radius: 26px; overflow: hidden;
    box-shadow: 0 18px 40px rgba(0,0,0,0.45);
  }
  /* Side 1: contact */
  .card--contact {
    left: 110px; top: 110px;
    background: var(--card-white);
  }
  .brand-art {
    position: absolute; left: 0; top: 90px; width: 220px; height: 230px;
    border-radius: 0 110px 0 26px;
    background: linear-gradient(170deg, var(--warm-orange) 0%, var(--warm-red) 30%, var(--mid-violet) 62%, var(--cool-blue) 100%);
  }
  .brand-name {
    position: absolute; right: 34px; top: 34px;
    font-family: "Montserrat", sans-serif; font-weight: 700;
    font-size: 40px; letter-spacing: 4px; text-transform: uppercase;
    color: var(--ink-dark);
  }
  .contact {
    position: absolute; right: 34px; top: 130px; text-align: right;
    color: var(--accent-cyan);
    font-family: "Montserrat", sans-serif;
  }
  .contact__name { font-weight: 700; font-size: 24px; letter-spacing: 0.5px; line-height: 1.1; }
  .contact__title { font-family: "Questrial", sans-serif; font-size: 17px; letter-spacing: 0.5px; }
  .contact__lines {
    margin-top: 26px;
    font-family: "Questrial", sans-serif; font-size: 16px; line-height: 1.35;
    text-transform: uppercase; letter-spacing: 0.5px;
  }
  /* Side 2: product */
  .card--product {
    left: 530px; top: 470px;
    background: linear-gradient(120deg, var(--grad-purple) 0%, var(--grad-blue) 50%, var(--grad-cyan) 100%);
    display: flex; flex-direction: column; align-items: center; justify-content: center;
    text-align: center;
  }
  .product-mark {
    display: flex; align-items: center; gap: 14px;
    font-family: "Montserrat", sans-serif; font-weight: 700;
    font-size: 50px; color: var(--card-white); letter-spacing: 0.5px;
  }
  .product-mark__dot {
    width: 22px; height: 22px; border-radius: 50%; background: var(--card-white);
  }
  .product-tagline {
    margin-top: 26px;
    font-family: "Questrial", sans-serif; font-size: 17px; letter-spacing: 0.6px;
    text-transform: uppercase; color: var(--tagline);
  }
  .product-url {
    margin-top: 6px;
    font-family: "Questrial", sans-serif; font-size: 17px; letter-spacing: 0.6px;
    text-transform: uppercase; color: var(--card-white);
  }
</style>
</head>
<body>
  <main class="canvas">
    <section class="card card--contact" aria-label="Contact side">
      <div class="brand-art" role="img" aria-label="Brand illustration in warm-to-cool gradient"></div>
      <div class="brand-name">Brightloom</div>
      <div class="contact">
        <p class="contact__name">PERRY DUNMORE</p>
        <p class="contact__title">FOUNDER &amp; CEO</p>
        <p class="contact__lines">pdunmore@quillpost-mail.net<br>(555)-014-2286</p>
      </div>
    </section>

    <section class="card card--product" aria-label="Product side">
      <div class="product-mark">
        <span class="product-mark__dot" aria-hidden="true"></span>
        <span>Glimworld</span>
      </div>
      <p class="product-tagline">Culturally Immersive Language Learning Games</p>
      <p class="product-url">www.glimworld-play.com</p>
    </section>
  </main>
</body>
</html>
```